Weightloss company needs Business Card

We want a business card that is clean and professional, yet portrays that we are a friendly, innovative, and versatile program designed to fit the needs of our clients.
I would like there to be 2 sides, one side having an appointment card, and the other side containing the logo and business information. There can be decorations on both sides. The logo is attached.

Target Market(s)

Men and women 40-60

Industry/Entity Type

Business

Contact Information for Business Card

Font styles to use
Sans Serif

Requirements
Must have
• The logo, space for business information
Nice to have
• The colors in the logo
Should not have
• No pictures of people or food

```html
<!DOCTYPE html>
<html lang="en">
<head>
<meta charset="utf-8">
<title>Renew Turn Wellness – Business Card</title>
<link href="https://fonts.googleapis.com/css2?family=Open+Sans:wght@400;600;700&display=swap" rel="stylesheet">
<style>
  :root {
    --backdrop: #2b2b2d;
    --card: #ffffff;
    --brand-red: #e8263b;
    --brand-blue: #3fb8e6;
    --faint-blue: #e3f4fc;
    --ink: #1c1c1c;
    --rule: #222222;
  }
  * { box-sizing: border-box; margin: 0; padding: 0; }
  html, body {
    width: 1200px; height: 900px; overflow: hidden;
    background: var(--backdrop);
    font-family: "Open Sans", sans-serif;
    color: var(--ink);
  }
  .card {
    position: absolute;
    width: 560px; height: 320px;
    background: var(--card);
    border-radius: 22px;
    overflow: hidden;
    box-shadow: 0 12px 30px rgba(0,0,0,.45);
  }
  .card--appointment { left: 70px; top: 110px; }
  .card--contact { left: 570px; top: 470px; }

  .brand {
    position: absolute;
    display: flex; align-items: center; gap: 10px;
    color: var(--brand-red);
    font-weight: 700;
    font-size: 26px;
    line-height: 1;
    white-space: nowrap;
  }
  .brand__dot {
    width: 18px; height: 18px; border-radius: 50%;
    background: var(--brand-red);
  }
  .card--appointment .brand { right: 34px; bottom: 64px; }
  .card--contact .brand { right: 34px; top: 62px; }

  .appointment__title {
    position: absolute; left: 40px; top: 56px;
    color: var(--brand-red); font-size: 14px; letter-spacing: .3px;
  }
  .appointment__field {
    position: absolute; left: 40px;
    display: flex; align-items: flex-end; gap: 8px;
    font-size: 14px;
  }
  .appointment__field span.line {
    display: block; height: 1px; background: var(--ink); margin-bottom: 4px;
  }
  .field--name { top: 92px; }
  .field--date { top: 134px; }
  .field--time { top: 176px; }

  .contact__rule {
    position: absolute; left: 0; right: 66px; top: 150px;
    height: 1.5px; background: var(--rule);
  }
  .contact__deco {
    position: absolute; left: 250px; top: 80px;
    width: 190px; height: 190px; border-radius: 50%;
    border: 14px solid var(--faint-blue);
  }
  .contact__address {
    position: absolute; right: 30px; top: 162px;
    text-align: right; font-size: 13px; line-height: 1.35;
  }
  .contact__person { position: absolute; left: 38px; top: 190px; }
  .contact__name { color: var(--brand-red); font-size: 22px; font-weight: 400; line-height: 1.1; letter-spacing: .3px; }
  .contact__role { color: var(--brand-blue); font-size: 12px; font-weight: 600; letter-spacing: .4px; }
  .contact__divider { width: 250px; height: 1.5px; background: var(--rule); margin: 6px 0 6px; }
  .contact__list { list-style: none; font-size: 14px; line-height: 1.4; }
  .contact__list li { display: flex; align-items: center; gap: 10px; }
  .contact__list svg { width: 12px; height: 12px; flex: none; }
</style>
</head>
<body>

<section class="card card--appointment" aria-label="Appointment side">
  <p class="appointment__title">APPOINTMENT</p>
  <div class="appointment__field field--name"><span>Name:</span><span class="line" style="width:320px"></span></div>
  <div class="appointment__field field--date"><span>Date:</span><span class="line" style="width:330px"></span></div>
  <div class="appointment__field field--time"><span>Time:</span><span class="line" style="width:330px"></span></div>
  <div class="brand"><span class="brand__dot"></span>Renew Turn Wellness</div>
</section>

<section class="card card--contact" aria-label="Contact side">
  <div class="contact__deco"></div>
  <div class="brand"><span class="brand__dot"></span>Renew Turn Wellness</div>
  <div class="contact__rule"></div>
  <address class="contact__address" style="font-style:normal">
    Palm Street, 20415<br>Harbor City, Coastland
  </address>
  <div class="contact__person">
    <h1 class="contact__name">MARLO PENNICK</h1>
    <p class="contact__role">DIRECTOR</p>
    <div class="contact__divider"></div>
    <ul class="contact__list">
      <li>
        <svg viewBox="0 0 12 12"><path d="M2.5 1 L4.5 1 L5.2 3.6 L4 4.6 Q5 7 7.4 8 L8.4 6.8 L11 7.5 L11 9.5 Q10 11 8 10.6 Q2 9 1.2 3 Q1 1.8 2.5 1Z" fill="var(--brand-red)"/></svg>
        +330 5550-1482
      </li>
      <li>
        <svg viewBox="0 0 12 12"><rect x="1" y="2.5" width="10" height="7" fill="none" stroke="var(--brand-red)" stroke-width="1.2"/><path d="M1 2.5 L6 6.5 L11 2.5" fill="none" stroke="var(--brand-red)" stroke-width="1.2"/></svg>
        info@renewturnwellness.com
      </li>
      <li>
        <svg viewBox="0 0 12 12"><circle cx="6" cy="6" r="5" fill="none" stroke="var(--brand-red)" stroke-width="1.2"/><path d="M1 6 H11 M6 1 Q3 6 6 11 Q9 6 6 1" fill="none" stroke="var(--brand-red)" stroke-width="1"/></svg>
        www.renewturnwellness.com
      </li>
    </ul>
  </div>
</section>

</body>
</html>
```